"Tandem Mouthguards " Custom-made Mouthguard Business Website

We need an informational website for our mouthguard Business "Tandem Mouthguards". The logo is navy blue/lime green so want to have colour scheme that goes nicely with this - have uploaded our mouthguard flyer with some information we need to put into the website but I do have more information to put in there.

Target Market(s)

Sports clubs, sportspeople, parents and kids, schools

Industry/Entity Type

Dental, Custom-made Sports Mouthguards

Coding

Coded - Design and coding required

Number of Pages Required

5+ page

Font styles to use
Serif
Sans Serif

Colors
0054AA
0677BA
7BADD7
CADEEF
E8F1F8
0094D4
00A9DD
6FCCEA
C7EBF8
E9F6FB
00AB8E
00BBA5
67D7C9
C6EFE9
E9F9F6
59FF00
82FF00
B8FF75
E3FFCB
F4FFEA
FFF300
FFF600
FEFA6F
FFFEC7
FFFEE8
FFC000
F8CF3A
FAE287
FDF2CF
FEFAEE
F0912C
F2A743
F7CA91
FBE8D2
FDF5EE
EE7325
F08F49
F5BC92
FAE3D3
FDF4ED

Requirements
Must have
• I want drop down pages, not one scrolling page. Different pages for each heading . Content uploaded - We need a general home page with lots of pictures and info that I'll provide. A page each dedicated to 1) About Us 2) Why choose a custom mouthguard? 3) Gallery 4) Contact Us. Will need logos from "Velora"
Nice to have
• Mainly use greens and blues, but happy to pop in some yellow/oranges/red oranges if it looks good

```html
<!DOCTYPE html>
<html lang="en">
<head>
<meta charset="utf-8">
<title>Tandem Mouthguards</title>
<link rel="stylesheet" href="https://fonts.googleapis.com/css2?family=Montserrat:wght@500;600;700;800&family=Lato:wght@400;700&display=swap">
<style>
:root{
  --navy:#0c2577;
  --navy-deep:#081a57;
  --navy-mid:#12308c;
  --green:#2fca22;
  --green-bright:#44d52c;
  --white:#ffffff;
  --ink:#333a4a;
  --muted:#5b6070;
  --line:#c9cfda;
  --pale:#eef1f6;
}
*{box-sizing:border-box;margin:0;padding:0}
html,body{width:1200px;height:4326px;overflow:hidden;background:var(--white)}
body{font-family:"Lato",sans-serif;color:var(--ink)}
.page{position:relative;width:1200px;height:4326px;overflow:hidden}
.abs{position:absolute}
.heading{font-family:"Montserrat",sans-serif;font-weight:800;color:var(--navy);letter-spacing:.5px}
.heading.center{left:0;width:1200px;text-align:center;font-size:40px;line-height:44px}
.heading.light{color:var(--white)}
.underline{position:absolute;height:4px;width:118px;background:var(--green);border-radius:2px}

/* header */
.site-header{left:0;top:0;width:1200px;height:81px;background:var(--white)}
.brand{left:134px;top:12px;font-family:"Montserrat",sans-serif;font-weight:800;color:var(--navy);line-height:1}
.brand .b1{font-size:30px;letter-spacing:1px;display:block}
.brand .b2{font-size:17px;letter-spacing:.6px;display:block;margin-top:2px}
.pill{top:0;height:34px;background:var(--navy);border-radius:0 0 17px 17px;border-radius:17px;color:var(--white);font-family:"Lato",sans-serif;font-size:12.5px;display:flex;align-items:center;padding-left:42px}
.pill b{font-weight:700}
.pill .dot{position:absolute;left:9px;top:6px;width:22px;height:22px;border-radius:50%;background:var(--green);display:flex;align-items:center;justify-content:center}
.nav{top:47px;font-size:15px;color:#2d3140;font-family:"Lato",sans-serif}
.nav.active{color:var(--green)}

/* hero */
.hero-photo{left:0;top:81px;width:1200px;height:760px;background:
 linear-gradient(180deg,rgba(12,37,119,0) 55%,rgba(12,37,119,.85) 88%,var(--navy) 100%),
 radial-gradient(ellipse at 30% 40%,#3e8f34 0%,#285f3a 40%,#1b3f7a 75%,#163288 100%)}
.blue-band{left:0;top:822px;width:1200px;height:448px;background:var(--navy)}
.watermark{left:0;top:800px;width:1200px;text-align:center;font-family:"Montserrat",sans-serif;font-weight:800;font-size:72px;letter-spacing:4px;color:rgba(255,255,255,.07);white-space:nowrap}
.hero-title{left:0;top:603px;width:1200px;text-align:center;font-family:"Montserrat",sans-serif;font-weight:800;font-size:42px;line-height:49px;color:var(--white);letter-spacing:.5px}
.hero-title .g{color:var(--green-bright)}
.btn-book{left:426px;top:725px;width:339px;height:52px;border-radius:26px;background:var(--white);color:var(--navy);font-family:"Montserrat",sans-serif;font-weight:700;font-size:14px;display:flex;align-items:center;padding-left:30px}
.arrow-btn{width:40px;height:40px;border-radius:50%;background:var(--white);display:flex;align-items:center;justify-content:center}
.go{position:absolute;width:28px;height:28px;border-radius:50%;background:var(--green);display:flex;align-items:center;justify-content:center}

/* about */
.about-card{left:144px;top:914px;width:911px;height:576px;background:var(--white);border-radius:50px;box-shadow:0 10px 40px rgba(12,37,119,.14)}
.about-photo{left:589px;top:936px;width:446px;height:534px;border-radius:40px;background:radial-gradient(ellipse at 55% 45%,#5e86d8 0%,#2447b8 40%,#1c38a6 70%,#b9a58e 100%)}
.about-title{left:206px;top:978px;font-size:40px;line-height:44px}
.about-text{left:206px;top:1051px;width:330px;font-size:12.8px;line-height:22.6px;color:#3a3f4d}
.about-text p+p{margin-top:22.6px}
.btn-outline{border:2px solid var(--navy);border-radius:24px;background:var(--white);color:var(--navy);font-family:"Montserrat",sans-serif;font-weight:700;font-size:12px;display:flex;align-items:center;padding-left:24px}

/* why */
.why{left:0;top:1270px;width:1200px;height:1183px}
.why-label{font-size:15px;line-height:24px;color:#4a4f5e;font-family:"Lato",sans-serif}
.why-label.right{text-align:right}
.center-photo{left:457px;top:1934px;width:284px;height:284px;border-radius:50%;background:radial-gradient(circle at 45% 50%,#d94444 0%,#e9e9e9 35%,#3a3a3a 60%,#ffffff 75%)}

/* gallery */
.gallery{left:0;top:2453px;width:1200px;height:782px;background:var(--navy)}
.g-tile{border:2px solid var(--white);border-radius:16px}
.zoom{position:absolute;left:571px;top:2723px;width:56px;height:56px;border-radius:50%;background:rgba(255,255,255,.85);display:flex;align-items:center;justify-content:center}

/* contact */
.contact-card{left:144px;top:3403px;width:378px;height:378px;border-radius:26px;background:var(--green)}
.contact-inner{left:171px;top:3432px;width:326px;height:322px;border-radius:22px;background:var(--navy)}
.c-ico{width:44px;height:44px;border-radius:50%;background:var(--green);display:flex;align-items:center;justify-content:center}
.c-label{font-family:"Montserrat",sans-serif;font-weight:700;font-size:17px;color:var(--white)}
.c-value{font-family:"Montserrat",sans-serif;font-weight:500;font-size:13.5px;line-height:23px;color:var(--white)}
.field{border:1.5px solid var(--line);border-radius:6px;background:var(--white);font-family:"Montserrat",sans-serif;font-size:14px;color:#444;padding:18px 0 0 18px}

/* footer */
.footer{left:0;top:3915px;width:1200px;height:347px;background:var(--navy)}
.footer-brand{left:149px;top:4012px;font-family:"Montserrat",sans-serif;font-weight:800;color:var(--white);line-height:1}
.footer-brand .b1{font-size:30px;letter-spacing:1px;display:block}
.footer-brand .b2{font-size:17px;letter-spacing:.6px;display:block;margin-top:2px}
.social{width:34px;height:34px;border-radius:50%;border:2px solid var(--white);display:flex;align-items:center;justify-content:center}
.social.on{background:var(--green)}
.f-head{font-family:"Montserrat",sans-serif;font-weight:700;font-size:19px;color:var(--white)}
.f-links{list-style:none;font-size:14px;color:var(--white);line-height:24.4px}
.f-links li{padding-left:24px;position:relative}
.f-links li::before{content:"";position:absolute;left:0;top:8px;width:8px;height:8px;border-radius:50%;background:var(--green)}
.f-item{font-size:13.5px;line-height:21px;color:var(--white);padding-left:24px}
.f-item b{display:block;font-weight:700}
.f-ico{position:absolute;left:0;top:3px}
.news-input{left:814px;top:4047px;width:246px;height:41px;border:1.5px solid rgba(255,255,255,.7);border-radius:21px;color:var(--white);font-size:13.5px;display:flex;align-items:center;padding-left:40px}
.btn-sub{left:814px;top:4096px;width:126px;height:37px;border-radius:19px;background:var(--green);color:var(--white);font-family:"Montserrat",sans-serif;font-weight:700;font-size:13.5px;display:flex;align-items:center;justify-content:center}
.bottom-bar{left:0;top:4262px;width:1200px;height:64px;background:var(--navy-deep)}
.partner{font-family:"Montserrat",sans-serif;font-weight:600;font-size:17px;color:var(--white)}
.copyright{left:0;top:4283px;width:1200px;text-align:center;font-size:14px;color:var(--white)}
</style>
</head>
<body>
<div class="page">

  <!-- Header -->
  <header class="abs site-header">
    <div class="abs brand"><span class="b1">TANDEM</span><span class="b2">MOUTHGUARDS</span></div>
    <div class="abs pill" style="left:498px;width:215px">
      <span class="dot"><svg width="12" height="12" viewBox="0 0 24 24"><path fill="#fff" d="M6.6 10.8a15 15 0 0 0 6.6 6.6l2.2-2.2a1 1 0 0 1 1-.25 11.4 11.4 0 0 0 3.6.57 1 1 0 0 1 1 1V20a1 1 0 0 1-1 1A17 17 0 0 1 3 4a1 1 0 0 1 1-1h3.5a1 1 0 0 1 1 1c0 1.25.2 2.45.57 3.57a1 1 0 0 1-.25 1z"/></svg></span>
      Call Us :&nbsp;<b>+1 555 010 2040</b>
    </div>
    <div class="abs pill" style="left:718px;width:342px">
      <span class="dot"><svg width="12" height="12" viewBox="0 0 24 24"><path fill="#fff" d="M2 5h20v14H2z M2 5l10 8 10-8" stroke="#2fca22" stroke-width="1.5"/></svg></span>
      Mail Us :&nbsp;<b>reception@harbourdenturestudio.com.au</b>
    </div>
    <nav>
      <span class="abs nav active" style="left:482px">Home</span>
      <span class="abs nav" style="left:557px">About</span>
      <span class="abs nav" style="left:636px">Our Mouthguards</span>
      <span class="abs nav" style="left:795px">Photo Gallery</span>
      <span class="abs nav" style="left:926px">FAQ</span>
      <span class="abs nav" style="left:992px">Contact</span>
    </nav>
  </header>

  <!-- Hero -->
  <div class="abs blue-band"></div>
  <div class="abs hero-photo" role="img" aria-label="Two young football players smiling while wearing colourful custom mouthguards, holding a yellow football"></div>
  <div class="abs watermark">TANDEM MOUTHGUARDS</div>
  <div class="abs arrow-btn" style="left:51px;top:369px"><svg width="14" height="14" viewBox="0 0 14 14"><path d="M9 2L4 7l5 5" fill="none" stroke="#0c2577" stroke-width="2"/></svg></div>
  <div class="abs arrow-btn" style="left:1109px;top:369px"><svg width="14" height="14" viewBox="0 0 14 14"><path d="M5 2l5 5-5 5" fill="none" stroke="#0c2577" stroke-width="2"/></svg></div>
  <h1 class="abs hero-title"><span class="g">PROTECT</span> YOUR SMILE.<br>PLAY WITH <span class="g">CONFIDENCE.</span></h1>
  <div class="abs btn-book">BOOK YOUR MOUTHGUARD TODAY
    <span class="go" style="left:300px;top:12px"><svg width="10" height="10" viewBox="0 0 10 10"><path d="M3 1l4 4-4 4" fill="none" stroke="#fff" stroke-width="1.8"/></svg></span>
  </div>

  <!-- About -->
  <section>
    <div class="abs about-card"></div>
    <div class="abs about-photo" role="img" aria-label="Blue marbled custom mouthguard sitting in an open blue storage case"></div>
    <h2 class="abs heading about-title">ABOUT ME</h2>
    <div class="underline" style="left:206px;top:1027px"></div>
    <div class="abs about-text">
      <p>My name is Tessa, and I am a dental prosthetist with over 20 years of experience in the dental field. I hold a Diploma of Dental Technology and an Advanced Diploma of Dental Prosthetics, which I obtained at Coastal Institute of Technology in 2011. At Tandem Mouthguards (inside my Harbour Denture Studio clinic), my work involves designing and making custom-fitted sports mouthguards for athletes of all ages.</p>
      <p>The goal is simple: provide mouthguards that fit well, feel comfortable, and offer reliable protection on the field, court, or in the ring. Every mouthguard is made individually, with close attention to detail, so that players can focus on their performance rather than worrying about their smile.</p>
    </div>
    <div class="abs btn-outline" style="left:210px;top:1400px;width:154px;height:43px">LEARN MORE
      <span class="go" style="left:111px;top:6px"><svg width="10" height="10" viewBox="0 0 10 10"><path d="M3 1l4 4-4 4" fill="none" stroke="#fff" stroke-width="1.8"/></svg></span>
    </div>
  </section>

  <!-- Why choose us -->
  <section class="abs why">
    <svg class="abs" style="left:0;top:0" width="1200" height="1183" viewBox="0 0 1200 1183">
      <circle cx="-10" cy="534" r="215" fill="none" stroke="#eef1f6" stroke-width="90"/>
      <circle cx="-10" cy="534" r="300" fill="none" stroke="#f3f9f1" stroke-width="18" stroke-dasharray="300 1600" transform="rotate(20 -10 534)"/>
      <path d="M389 927 A242 242 0 1 1 809 927" fill="none" stroke="#e3e7ef" stroke-width="4"/>
      <circle cx="599" cy="806" r="193" fill="#0c2577"/>
      <circle cx="599" cy="806" r="146" fill="#ffffff"/>
      <path d="M447 958 A215 215 0 0 0 751 958" fill="none" stroke="#2fca22" stroke-width="12"/>
      <path d="M456 1011 A250 250 0 0 0 742 1011" fill="none" stroke="#2fca22" stroke-width="8"/>
      <path d="M463 1062 A290 290 0 0 0 735 1062" fill="none" stroke="#2fca22" stroke-width="6"/>
      <!-- connector dots -->
      <g fill="#fff" stroke="#0c2577" stroke-width="3">
        <circle cx="599" cy="564" r="8"/><circle cx="441" cy="616" r="8"/><circle cx="753" cy="616" r="8"/>
        <circle cx="357" cy="816" r="8"/><circle cx="836" cy="816" r="8"/>
      </g>
      <!-- top: colours -->
      <path d="M588 526 L599 544 L610 526 Z" fill="#0c2577"/>
      <circle cx="599" cy="467" r="56" fill="#fff" stroke="#0c2577" stroke-width="12"/>
      <g fill="#0c2577"><path d="M599 447a16 16 0 0 1 9 29v6h-18v-6a16 16 0 0 1 9-29z"/><rect x="591" y="485" width="16" height="4"/><rect x="593" y="491" width="12" height="3"/>
        <rect x="571" y="462" width="8" height="3"/><rect x="619" y="462" width="8" height="3"/><rect x="597" y="433" width="3" height="8"/></g>
      <!-- left: custom fit -->
      <path d="M402 605 L420 616 L402 627 Z" fill="#2fca22"/>
      <circle cx="346" cy="616" r="56" fill="#fff" stroke="#2fca22" stroke-width="12"/>
      <g fill="#2fca22"><circle cx="346" cy="616" r="20"/><g stroke="#2fca22" stroke-width="7"><path d="M346 590v52M320 616h52M328 598l36 36M364 598l-36 36"/></g></g>
      <circle cx="346" cy="616" r="8" fill="#fff"/>
      <!-- right: people -->
      <path d="M795 605 L777 616 L795 627 Z" fill="#2fca22"/>
      <circle cx="851" cy="616" r="56" fill="#fff" stroke="#2fca22" stroke-width="12"/>
      <g fill="#2fca22"><circle cx="851" cy="601" r="9"/><circle cx="833" cy="607" r="7"/><circle cx="869" cy="607" r="7"/>
        <path d="M836 636v-12a15 12 0 0 1 30 0v12z"/><path d="M821 636v-9a12 10 0 0 1 14-9v18z"/><path d="M881 636v-9a12 10 0 0 0-14-9v18z"/></g>
      <!-- lower left: tooth -->
      <path d="M318 803 L336 814 L318 825 Z" fill="#0c2577"/>
      <circle cx="262" cy="814" r="56" fill="#fff" stroke="#0c2577" stroke-width="12"/>
      <path d="M248 795c8-3 10 3 14 3s6-6 14-3c9 4 7 18 3 26-2 5-3 16-7 16s-4-13-10-13-6 13-10 13-5-11-7-16c-4-8-6-22 3-26z" fill="#0c2577"/>
      <!-- lower right: clinic -->
      <path d="M877 803 L859 814 L877 825 Z" fill="#0c2577"/>
      <circle cx="933" cy="814" r="56" fill="#fff" stroke="#0c2577" stroke-width="12"/>
      <g fill="#0c2577"><rect x="911" y="806" width="44" height="28"/><rect x="920" y="794" width="26" height="14"/></g>
      <g fill="#fff"><rect x="931" y="797" width="4" height="9"/><rect x="928" y="800" width="10" height="3"/><rect x="916" y="813" width="6" height="16"/><rect x="930" y="813" width="6" height="16"/><rect x="944" y="813" width="6" height="16"/></g>
    </svg>
    <h2 class="abs heading center" style="top:315px">WHY CHOOSE US</h2>
    <div class="underline" style="left:541px;top:364px"></div>
  </section>
  <div class="abs center-photo" role="img" aria-label="Patterned red, white and black checkered custom mouthguards"></div>
  <div class="abs why-label right" style="left:300px;top:1703px;width:220px">Wide range of colours<br>and designs</div>
  <div class="abs why-label right" style="left:60px;top:1893px;width:219px">Custom fit for comfort,<br>protection, and durability</div>
  <div class="abs why-label" style="left:925px;top:1893px;width:200px">Available for kids,<br>teens, and adults</div>
  <div class="abs why-label right" style="left:120px;top:2154px;width:199px">Professionally made by<br>a qualified dental<br>prosthetist</div>
  <div class="abs why-label" style="left:868px;top:2151px;width:180px">Clinic and mobile<br>school/club visits<br>available</div>

  <!-- Gallery -->
  <section class="abs gallery"></section>
  <h2 class="abs heading center light" style="top:2543px">OUR GALLERY</h2>
  <div class="underline" style="left:541px;top:2594px"></div>
  <div class="abs g-tile" style="left:144px;top:2634px;width:282px;height:495px;background:linear-gradient(160deg,#8a62c9,#5b3aa0 55%,#caa38f)" role="img" aria-label="Hand holding purple glitter mouthguards"></div>
  <div class="abs g-tile" style="left:460px;top:2634px;width:282px;height:234px;background:radial-gradient(ellipse at 50% 50%,#2a3a6a,#1b2338 60%,#5a6a8a)" role="img" aria-label="Dark speckled confetti mouthguard"></div>
  <div class="zoom"><svg width="20" height="20" viewBox="0 0 20 20"><path d="M10 3v14M3 10h14" stroke="#0c2577" stroke-width="2.5"/></svg></div>
  <div class="abs g-tile" style="left:460px;top:2898px;width:282px;height:231px;background:linear-gradient(90deg,#c6201c,#7a1714 45%,#e8dada 65%,#f1c7c7)" role="img" aria-label="Red and pink mouthguards in open cases"></div>
  <div class="abs g-tile" style="left:774px;top:2634px;width:283px;height:495px;background:linear-gradient(180deg,#efefef,#d9d9d9 40%,#8a1f2a 62%,#d6c9bb 85%,#b58a5c)" role="img" aria-label="Maroon school mouthguard in a white case"></div>
  <div class="abs arrow-btn" style="left:51px;top:2861px"><svg width="14" height="14" viewBox="0 0 14 14"><path d="M9 2L4 7l5 5" fill="none" stroke="#0c2577" stroke-width="2"/></svg></div>
  <div class="abs arrow-btn" style="left:1109px;top:2861px"><svg width="14" height="14" viewBox="0 0 14 14"><path d="M5 2l5 5-5 5" fill="none" stroke="#0c2577" stroke-width="2"/></svg></div>

  <!-- Contact -->
  <svg class="abs" style="left:700px;top:3300px" width="500" height="620" viewBox="0 0 500 620">
    <circle cx="330" cy="320" r="200" fill="none" stroke="#eef1f6" stroke-width="70"/>
    <path d="M120 500 A260 260 0 0 0 480 560" fill="none" stroke="#f2faef" stroke-width="16"/>
  </svg>
  <h2 class="abs heading center" style="top:3312px">CONTACT US</h2>
  <div class="underline" style="left:541px;top:3364px"></div>
  <div class="abs contact-card"></div>
  <div class="abs contact-inner"></div>
  <div class="abs c-ico" style="left:211px;top:3490px"><svg width="16" height="18" viewBox="0 0 16 20"><path d="M8 0a7 7 0 0 1 7 7c0 5-7 13-7 13S1 12 1 7a7 7 0 0 1 7-7z" fill="#fff"/><circle cx="8" cy="7" r="2.6" fill="#2fca22"/></svg></div>
  <div class="abs c-label" style="left:272px;top:3488px">Address :</div>
  <div class="abs c-value" style="left:272px;top:3518px">Unit 4/12 Meridian Way,<br>Eastfield WA 6100</div>
  <div class="abs" style="left:213px;top:3596px;width:246px;height:1px;background:rgba(255,255,255,.25)"></div>
  <div class="abs c-ico" style="left:211px;top:3623px"><svg width="16" height="16" viewBox="0 0 24 24"><path fill="#fff" d="M6.6 10.8a15 15 0 0 0 6.6 6.6l2.2-2.2a1 1 0 0 1 1-.25 11.4 11.4 0 0 0 3.6.57 1 1 0 0 1 1 1V20a1 1 0 0 1-1 1A17 17 0 0 1 3 4a1 1 0 0 1 1-1h3.5a1 1 0 0 1 1 1c0 1.25.2 2.45.57 3.57a1 1 0 0 1-.25 1z"/></svg></div>
  <div class="abs c-label" style="left:272px;top:3622px">Phone :</div>
  <div class="abs c-value" style="left:272px;top:3654px">08 5550 1234</div>
  <div class="abs field" style="left:545px;top:3403px;width:245px;height:55px">First name</div>
  <div class="abs field" style="left:810px;top:3403px;width:245px;height:55px">Last name</div>
  <div class="abs field" style="left:545px;top:3475px;width:245px;height:56px">Email</div>
  <div class="abs field" style="left:810px;top:3475px;width:245px;height:56px">Phone</div>
  <div class="abs field" style="left:545px;top:3547px;width:510px;height:175px">Message</div>
  <div class="abs btn-outline" style="left:542px;top:3739px;width:154px;height:43px;padding-left:18px">SUBMIT NOW
    <span class="go" style="left:115px;top:6px"><svg width="10" height="10" viewBox="0 0 10 10"><path d="M3 1l4 4-4 4" fill="none" stroke="#fff" stroke-width="1.8"/></svg></span>
  </div>

  <!-- Footer -->
  <footer class="abs footer"></footer>
  <div class="abs footer-brand"><span class="b1">TANDEM</span><span class="b2">MOUTHGUARDS</span></div>
  <div class="abs social" style="left:176px;top:4126px"></div>
  <div class="abs social on" style="left:216px;top:4126px"></div>
  <div class="abs social" style="left:255px;top:4126px"></div>

  <div class="abs f-head" style="left:393px;top:4005px">QUICK LINKS</div>
  <ul class="abs f-links" style="left:393px;top:4052px">
    <li>Home</li><li>About us</li><li>Our Mouthguards</li><li>Blog</li><li>Reviews</li><li>FAQ</li><li>Contact us</li>
  </ul>

  <div class="abs f-head" style="left:584px;top:4005px">CONTACT US</div>
  <div class="abs f-item" style="left:584px;top:4046px;width:200px">
    <svg class="f-ico" width="11" height="14" viewBox="0 0 16 20"><path d="M8 0a7 7 0 0 1 7 7c0 5-7 13-7 13S1 12 1 7a7 7 0 0 1 7-7z" fill="#2fca22"/></svg>
    <b>Address :</b>Unit 4/12 Meridian Way,<br>Eastfield WA 6100</div>
  <div class="abs f-item" style="left:584px;top:4128px;width:200px">
    <svg class="f-ico" width="12" height="12" viewBox="0 0 24 24"><path fill="#2fca22" d="M6.6 10.8a15 15 0 0 0 6.6 6.6l2.2-2.2a1 1 0 0 1 1-.25 11.4 11.4 0 0 0 3.6.57 1 1 0 0 1 1 1V20a1 1 0 0 1-1 1A17 17 0 0 1 3 4a1 1 0 0 1 1-1h3.5a1 1 0 0 1 1 1c0 1.25.2 2.45.57 3.57a1 1 0 0 1-.25 1z"/></svg>
    <b>Phone :</b>08 5550 1234</div>
  <div class="abs f-item" style="left:584px;top:4192px;width:260px">
    <svg class="f-ico" width="13" height="11" viewBox="0 0 24 18"><rect width="24" height="18" rx="2" fill="#2fca22"/><path d="M2 2l10 8 10-8" fill="none" stroke="#0c2577" stroke-width="2"/></svg>
    <b>Email Address :</b>reception@harbourdenturestudio.com.au</div>

  <div class="abs f-head" style="left:814px;top:4005px">OUR NEWSLETTER</div>
  <div class="abs news-input">
    <svg class="abs" style="left:16px;top:15px" width="13" height="11" viewBox="0 0 24 18"><rect width="24" height="18" rx="2" fill="#fff"/><path d="M2 2l10 8 10-8" fill="none" stroke="#0c2577" stroke-width="2"/></svg>
    Email address</div>
  <div class="abs btn-sub">SUBSCRIBE</div>

  <div class="abs bottom-bar"></div>
  <div class="abs partner" style="left:148px;top:4282px">Harbour Denture Studio</div>
  <div class="abs copyright">© Copyrights 2025 | All Rights Reserved</div>
  <div class="abs" style="left:923px;top:4285px;width:16px;height:16px;border-radius:50%;background:#f2c21b"></div>
  <div class="abs partner" style="left:946px;top:4281px;font-size:20px">VELORA</div>

</div>
</body>
</html>
```